Teach English in China Website Redesign Needed

We recruit native English speakers from the US, UK, etc. who want to teach English as a foreign language in schools in China. Our target customer is college educated, age 22-28 and they love to travel. We prefer designs with bright colors and lots of photos. We want to keep all the text on our current homepage, BrightLanternPost.com. We are open to changing our logo. A competitor's page that we like is pinemeadowtutors.com because of their bright colors, photos and use of white space. We are happy to give you a dofollow link and design credit on our homepage. The use of included photos is optional. We need at least a home page design and a standard blog post design.
Target Market(s)
Our target customer is college educated, age 22-28 and they love to travel. Half of our customers are kindergarten teachers. Half of our customers are male.
Logo Text
Bright Lantern Post
Requirements
Must have
- Bright colors
Should not have
- Our homepage must not look crowded. Use white space effectively.

```html
<!DOCTYPE html>
<html lang="en">
<head>
<meta charset="utf-8">
<title>Bright Lantern Post — Teach English in China</title>
<link href="https://fonts.googleapis.com/css2?family=Montserrat:wght@400;600;700&family=Open+Sans:wght@400;600;700&display=swap" rel="stylesheet">
<style>
:root{
  --red:#e3262c;
  --red-dark:#c21c22;
  --ink:#2a2a2a;
  --muted:#777;
  --line:#e2e2e2;
  --lavender:#e8e7f2;
  --footer:#1f1f1f;
  --footer-bar:#111;
  --white:#fff;
}
*{box-sizing:border-box;margin:0;padding:0}
html,body{width:1200px;height:3920px;overflow:hidden}
body{font-family:"Open Sans",Arial,sans-serif;color:var(--ink);background:var(--white);font-size:13px;line-height:1.6}
h1,h2,h3,h4{font-family:"Montserrat",Arial,sans-serif}
.accent{color:var(--red)}
.section-title{text-align:center;font-size:26px;font-weight:700;letter-spacing:.5px}
.section-title::after{content:"";display:block;width:44px;height:3px;background:var(--red);margin:12px auto 0}

/* header */
.site-header{height:90px;display:flex;align-items:center;justify-content:space-between;padding:0 80px;background:var(--white)}
.brand{display:flex;align-items:center;gap:10px;font-family:"Montserrat",sans-serif;font-weight:700;font-size:22px;color:var(--ink)}
.brand-mark{width:16px;height:16px;background:var(--red);border-radius:50%}
.main-nav{display:flex;align-items:center;gap:26px;font-family:"Montserrat",sans-serif;font-size:12px;font-weight:600}
.btn{display:inline-block;background:var(--red);color:var(--white);font-family:"Montserrat",sans-serif;font-weight:600;font-size:12px;padding:9px 20px;border-radius:2px}
.btn-dark{background:#2b2b2b}
.social{display:flex;gap:9px}
.social span{width:11px;height:11px;border-radius:50%;background:#555;display:block}

/* hero */
.hero{height:410px;position:relative;background:linear-gradient(180deg,#b9c3cf 0%,#8d9aa3 35%,#5f6f4d 65%,#3f4b35 85%,#8b2c1f 100%);display:flex;flex-direction:column;align-items:center;justify-content:center}
.hero-scene{position:absolute;inset:0}
.hero h1{position:relative;color:var(--white);font-size:48px;font-weight:700;letter-spacing:1px;margin-top:-20px}
.search-bar{position:relative;display:flex;gap:10px;margin-top:26px}
.search-bar .field{width:170px;height:44px;background:var(--white);border-radius:2px;padding:0 14px;display:flex;align-items:center;color:#999;font-size:12px}
.search-bar .btn{height:44px;width:156px;display:flex;align-items:center;justify-content:center;gap:8px;font-size:14px}

/* jobs */
.jobs{height:860px;padding-top:48px}
.card-row{display:flex;justify-content:space-between;padding:0 88px;margin-top:52px}
.job-card{width:310px;text-align:center;padding-bottom:20px}
.job-card.is-featured{box-shadow:0 6px 22px rgba(0,0,0,.14);padding:0 0 26px}
.job-photo{height:250px;border-radius:2px}
.job-card h3{font-size:15px;font-weight:600;margin:22px 22px 12px;line-height:1.5}
.job-card.is-featured h3{color:var(--red)}
.job-card p{color:var(--muted);font-size:12px;margin:0 26px 28px}

/* apply */
.apply{height:340px;background:var(--lavender);display:flex;align-items:center;justify-content:space-between;padding:0 90px;position:relative;margin-top:20px}
.apply-copy{width:560px}
.apply-copy h2{font-size:28px;font-weight:700;margin-bottom:14px}
.apply-copy p{color:#555;font-size:13px;margin-bottom:24px}
.apply .btn{padding:14px 30px;font-size:14px}
.apply-photo{width:300px;height:340px;align-self:flex-end;background:linear-gradient(180deg,#d8d2cc,#9b7a64 45%,#6f6e74);border-radius:2px}

/* articles */
.articles{height:790px;padding-top:54px}
.article-card{width:310px}
.article-photo{height:230px;position:relative}
.date-badge{position:absolute;right:14px;bottom:-20px;width:52px;height:56px;background:var(--red);color:var(--white);text-align:center;font-family:"Montserrat",sans-serif;line-height:1.1;padding-top:8px}
.date-badge b{display:block;font-size:20px}
.date-badge small{font-size:11px}
.article-card h3{font-size:15px;font-weight:600;margin:26px 0 6px;line-height:1.45}
.article-card.is-featured h3{color:var(--red)}
.byline{font-size:11px;color:#999;margin-bottom:14px}
.article-card p{font-size:12px;color:var(--muted);margin-bottom:18px}
.read-more{font-size:12px;color:var(--red);font-weight:600}

/* testimonials */
.testimonials{height:640px;background:linear-gradient(180deg,#2a2220,#4a2c24 50%,#2b2421);position:relative;padding-top:56px}
.testimonials .section-title{color:var(--white)}
.quote-row{display:flex;justify-content:center;align-items:flex-start;gap:40px;margin-top:60px}
.quote{width:300px;background:var(--white);border-radius:3px;padding:24px;font-size:12px;color:#555;position:relative;text-align:left}
.quote.is-featured{width:330px;padding:44px 28px 30px;margin-top:-24px}
.quote-icon{position:absolute;top:-22px;left:24px;width:44px;height:44px;background:var(--red);border-radius:50%;display:flex;align-items:center;justify-content:center}
.person{display:flex;flex-direction:column;align-items:center;margin-top:22px}
.avatar{width:92px;height:92px;border-radius:50%;border:4px solid var(--white);background:linear-gradient(160deg,#c9a78c,#6b4b3e)}
.name-tag{margin-top:-10px;background:var(--red);color:var(--white);font-size:11px;font-weight:600;padding:4px 16px;border-radius:2px;position:relative}
.quote-col{display:flex;flex-direction:column;align-items:center}

/* schools */
.schools{height:320px;padding-top:56px}
.school-row{display:flex;justify-content:space-between;padding:0 88px;margin-top:48px}
.school{width:190px;height:96px;border:1px solid var(--line);display:flex;align-items:center;justify-content:center}
.school.is-featured{border:2px solid var(--red)}
.school span{width:54px;height:54px;border-radius:50%;background:#d4d4d4}

/* footer */
.site-footer{height:400px;background:var(--footer);color:#bbb;display:flex;justify-content:space-between;padding:50px 88px 0}
.site-footer h4{color:var(--white);font-size:14px;font-weight:700;margin-bottom:22px}
.footer-col{width:300px}
.contact-line{display:flex;gap:12px;align-items:flex-start;font-size:12px;margin-bottom:16px}
.contact-line svg{flex:none;margin-top:3px}
.f-input{height:34px;border:1px solid #444;background:#2a2a2a;margin-bottom:10px;padding:0 12px;display:flex;align-items:center;font-size:11px;color:#888}
.f-area{height:70px;align-items:flex-start;padding-top:8px}
.newsletter-field{display:flex;margin-top:18px}
.newsletter-field .f-input{flex:1;background:var(--white);border:none;margin:0}
.newsletter-field .go{width:40px;height:34px;background:var(--red);display:flex;align-items:center;justify-content:center}
.footer-social{display:flex;gap:12px;margin-top:24px}
.footer-social span{width:14px;height:14px;border-radius:50%;background:#888;display:block}
.footer-bar{height:50px;background:var(--footer-bar);display:flex;align-items:center;justify-content:space-between;padding:0 88px;font-size:10px;color:#888}
.footer-bar nav{display:flex;gap:18px;color:#ccc;font-weight:600}
</style>
</head>
<body>

<header class="site-header">
  <div class="brand"><span class="brand-mark"></span>Bright Lantern Post</div>
  <nav class="main-nav">
    <span>HOME</span><span>AVAILABLE JOBS</span><span>APPLY ONLINE</span><span>BLOG</span><span>FAQ</span>
    <span class="btn">APPLY NOW</span>
    <span class="social"><span></span><span></span><span></span><span></span><span></span></span>
  </nav>
</header>

<section class="hero">
  <div class="hero-scene" role="img" aria-label="Great Wall winding over green mountains with red autumn trees in the foreground"></div>
  <h1>YOUR CAREER STARTS NOW</h1>
  <div class="search-bar">
    <div class="field">Keyword</div>
    <div class="field">Select Category</div>
    <div class="field">Location</div>
    <div class="btn">
      <svg width="14" height="14" viewBox="0 0 14 14"><circle cx="6" cy="6" r="4.5" fill="none" stroke="#fff" stroke-width="2"/><line x1="9.5" y1="9.5" x2="13" y2="13" stroke="#fff" stroke-width="2"/></svg>
      SEARCH
    </div>
  </div>
</section>

<section class="jobs">
  <h2 class="section-title">RECENT <span class="accent">AVAILABLE JOBS</span></h2>
  <div class="card-row">
    <article class="job-card">
      <div class="job-photo" role="img" aria-label="Bright school hallway with green walls" style="background:linear-gradient(160deg,#e6eecf,#9fbf5a 55%,#5f7d3a)"></div>
      <h3>Teach Students Ages 3 to Adult in Nanjing, Wuxi, Ningbo, Shenyang, Chongqing or Hefei</h3>
      <p>Private schools seek friendly native speakers for small classes. Paid flight, housing and full visa support are included.</p>
      <span class="btn btn-dark">Read More &gt;</span>
    </article>
    <article class="job-card is-featured">
      <div class="job-photo" role="img" aria-label="City skyline beside a river under a blue sky" style="background:linear-gradient(180deg,#8fb4d8,#b9cbd8 45%,#6f8a6b 75%,#4f6a55)"></div>
      <h3>Teach Children Mian City in Sichuan Province</h3>
      <p>Salary 10,000 to 12,000 RMB per month with free housing, paid holidays and a local team who help you settle in quickly.</p>
      <span class="btn">Read More &gt;</span>
    </article>
    <article class="job-card">
      <div class="job-photo" role="img" aria-label="Young children at tables in a colourful classroom" style="background:linear-gradient(160deg,#f1d9b5,#d98c5a 50%,#7a8fb0)"></div>
      <h3>Maple Sprout Preschool Job at Hillview Academy</h3>
      <p>A sunny kindergarten seeks a warm, patient teacher for small classes. Training is given and no prior work is required.</p>
      <span class="btn btn-dark">Read More &gt;</span>
    </article>
  </div>
</section>

<section class="apply">
  <div class="apply-copy">
    <h2>APPLY <span class="accent">NOW</span></h2>
    <p>Please make sure you read our FREQUENTLY ASKED QUESTIONS before submitting your information. For example, the FAQ page explains that you must hold a four year degree and a valid passport to apply.</p>
    <span class="btn">APPLY NOW</span>
  </div>
  <div class="apply-photo" role="img" aria-label="Smiling young teacher with long brown hair"></div>
</section>

<section class="articles">
  <h2 class="section-title">RECENT <span class="accent">ARTICLES</span></h2>
  <div class="card-row">
    <article class="article-card">
      <div class="article-photo" role="img" aria-label="Teacher standing in front of a classroom" style="background:linear-gradient(160deg,#cfc8bf,#8a8078 55%,#4d4a47)">
        <div class="date-badge"><b>24</b><small>JAN</small></div>
      </div>
      <h3>5 Huge Mistakes My First Year Teaching English in China</h3>
      <div class="byline">By Bright Lantern Post</div>
      <p>When my first year ended I made a list of what I wish I had known before arriving. Here are the five biggest lessons learned.</p>
      <span class="read-more">Read More &gt;</span>
    </article>
    <article class="article-card is-featured">
      <div class="article-photo" role="img" aria-label="Colourful event poster with red and yellow banners" style="background:linear-gradient(160deg,#f3d04a,#e6932d 45%,#b8262a)">
        <div class="date-badge"><b>24</b><small>JAN</small></div>
      </div>
      <h3>Marlo's ESL Lounge Job Fair for Teachers</h3>
      <div class="byline">By Bright Lantern Post</div>
      <p>If you are curious about teaching abroad, join our live chat this week and ask real teachers anything about life in China.</p>
      <span class="read-more">Read More &gt;</span>
    </article>
    <article class="article-card">
      <div class="article-photo" role="img" aria-label="Large hall filled with rows of students at desks" style="background:linear-gradient(160deg,#b9b7ae,#6f7c72 50%,#3c4640)">
        <div class="date-badge"><b>24</b><small>JAN</small></div>
      </div>
      <h3>How China Can Get Enough English Language Teachers</h3>
      <div class="byline">By Bright Lantern Post</div>
      <p>Demand for native speakers keeps rising each year. We look at what schools are doing to attract and keep great teachers.</p>
      <span class="read-more">Read More &gt;</span>
    </article>
  </div>
</section>

<section class="testimonials">
  <div class="hero-scene" role="img" aria-label="Group of teachers and students in a dim classroom"></div>
  <h2 class="section-title" style="position:relative">TEACHERS TESTIMONIALS</h2>
  <div class="quote-row" style="position:relative">
    <div class="quote-col">
      <div class="quote">My year in Hefei gave me confidence, friends and a career path I never expected. The support team was there at every step.</div>
      <div class="person"><div class="avatar" role="img" aria-label="Teacher portrait"></div><span class="name-tag">Adam Reyes</span></div>
    </div>
    <div class="quote-col">
      <div class="quote is-featured">
        <span class="quote-icon"><svg width="18" height="14" viewBox="0 0 18 14"><path d="M0 14V8C0 3 2 1 7 0v3C4 4 4 6 4 7h3v7zM11 14V8c0-5 2-7 7-8v3c-3 1-3 3-3 4h3v7z" fill="#fff"/></svg></span>
        When I began my search for a teaching job in China I felt nervous about the paperwork, but every question was answered quickly. My school was welcoming and my students made each day fun and rewarding.
      </div>
      <div class="person"><div class="avatar" role="img" aria-label="Teacher portrait"></div><span class="name-tag">Nora Whitfield</span></div>
    </div>
    <div class="quote-col">
      <div class="quote">Teaching kindergarten in Ningbo was the best decision I made after college. I saved money and travelled all over Asia.</div>
      <div class="person"><div class="avatar" role="img" aria-label="Teacher portrait"></div><span class="name-tag">Liam Porter</span></div>
    </div>
  </div>
</section>

<section class="schools">
  <h2 class="section-title">OUR <span class="accent">SCHOOLS</span></h2>
  <div class="school-row">
    <div class="school"><span></span></div>
    <div class="school"><span style="border-radius:4px;width:80px;height:34px"></span></div>
    <div class="school is-featured"><span></span></div>
    <div class="school"><span style="border-radius:6px"></span></div>
    <div class="school"><span></span></div>
  </div>
</section>

<footer class="site-footer">
  <div class="footer-col">
    <h4>CONTACT US</h4>
    <div class="contact-line"><svg width="12" height="14" viewBox="0 0 12 14"><path d="M6 0a5 5 0 0 0-5 5c0 4 5 9 5 9s5-5 5-9a5 5 0 0 0-5-5zm0 7a2 2 0 1 1 0-4 2 2 0 0 1 0 4z" fill="#e3262c"/></svg>4218 Harbor Crest Ave, Millbrook, Texas 77001</div>
    <div class="contact-line"><svg width="12" height="12" viewBox="0 0 12 12"><path d="M2 0l2.5 2.5-1.5 2a7 7 0 0 0 4.5 4.5l2-1.5L12 10l-2 2C4 12 0 8 0 2z" fill="#e3262c"/></svg>555-014-2290</div>
    <div class="contact-line"><svg width="14" height="10" viewBox="0 0 14 10"><rect width="14" height="10" fill="#e3262c"/><path d="M0 0l7 5 7-5" fill="none" stroke="#1f1f1f" stroke-width="1.2"/></svg>hello@brightlanternpost.com</div>
    <div class="footer-social"><span></span><span></span><span></span><span></span></div>
  </div>
  <div class="footer-col">
    <h4>SEND US A MESSAGE</h4>
    <div class="f-input">Name</div>
    <div class="f-input">Email</div>
    <div class="f-input f-area">Message</div>
    <span class="btn" style="padding:6px 18px">Send</span>
  </div>
  <div class="footer-col">
    <h4>NEWSLETTER SUBSCRIBE</h4>
    <p style="font-size:12px">Subscribe to our newsletter and we will inform you about newest jobs.</p>
    <div class="newsletter-field">
      <div class="f-input">Your email</div>
      <span class="go"><svg width="14" height="12" viewBox="0 0 14 12"><path d="M0 0l14 6-14 6 2-6z" fill="#fff"/></svg></span>
    </div>
  </div>
</footer>
<div class="footer-bar">
  <nav><span>HOME</span><span>AVAILABLE JOBS</span><span>APPLY ONLINE</span><span>BLOG</span><span>FAQ</span></nav>
  <span>Copyright © 2024 Bright Lantern Post. All Rights Reserved.</span>
</div>

</body>
</html>
```